Maple Roster Business Card for recruitment company

We are looking for a Business Card Design that incorporates our personal details and our busines name and logo. We are a specialized search consultancy that recruit Property and Construction professionals.
We would like a business card that stands out and is appealing to the Construction and Property industry as well.

Target Market(s)

people in the construction and property industry

Contact Information for Business Card

Business Name and logo

Font styles to use
Serif

Colors
0094D4
00A9DD
6FCCEA
C7EBF8
E9F6FB

Requirements
Must have
• Business name and logo as well as contact details
Should not have
• No photos of us please

```html
<!DOCTYPE html>
<html lang="en">
<head>
<meta charset="utf-8">
<title>Maple Roster – Business Card</title>
<link rel="stylesheet" href="https://fonts.googleapis.com/css2?family=Josefin+Sans:wght@300;400&family=Montserrat:wght@400;600;700&display=swap">
<style>
  :root {
    --page-bg: #2b2b2b;
    --card-dark: #3b3b3c;
    --card-light: #555657;
    --accent: #38b6de;
    --text-light: #ffffff;
    --text-soft: #e6e6e6;
  }
  * { box-sizing: border-box; margin: 0; padding: 0; }
  html, body {
    width: 1200px;
    height: 915px;
    overflow: hidden;
    background: var(--page-bg);
  }
  .canvas {
    position: relative;
    width: 1200px;
    height: 915px;
  }
  .card {
    position: absolute;
    width: 463px;
    height: 276px;
    overflow: hidden;
    background: linear-gradient(160deg, var(--card-dark) 0%, var(--card-light) 100%);
    box-shadow: 0 8px 22px rgba(0, 0, 0, 0.45);
    font-family: "Montserrat", sans-serif;
    color: var(--text-light);
  }
  .card--front { left: 505px; top: 176px; }
  .card--back  { left: 170px; top: 492px; }

  .band {
    position: absolute;
    height: 12px;
    background: var(--accent);
  }
  .band--top-right-cut { clip-path: polygon(0 0, 100% 0, calc(100% - 10px) 100%, 0 100%); }
  .band--bottom-left-cut { clip-path: polygon(10px 0, 100% 0, 100% 100%, 0 100%); }

  .card--front .band--top { top: 0; left: 13%; width: 62%; }
  .card--front .band--bottom { bottom: 0; left: 25%; width: 75%; }
  .card--back .band--top { top: 0; left: 25%; width: 60%; }
  .card--back .band--bottom { bottom: 0; left: 0; width: 75%; }

  .wordmark {
    position: absolute;
    font-family: "Josefin Sans", sans-serif;
    font-weight: 300;
    text-transform: uppercase;
    color: var(--text-light);
    white-space: nowrap;
  }
  .card--front .wordmark {
    left: 0; right: 0; top: 106px;
    text-align: center;
    font-size: 52px;
    letter-spacing: 0.5px;
  }
  .card--back .wordmark {
    left: 12px; top: 37px;
    font-size: 34px;
    letter-spacing: 0.3px;
  }

  .contact-list {
    position: absolute;
    left: 12px;
    top: 158px;
    list-style: none;
    font-size: 10.5px;
    letter-spacing: 1.2px;
    color: var(--text-soft);
  }
  .contact-list li {
    display: flex;
    align-items: center;
    gap: 7px;
    height: 17px;
  }
  .icon { width: 14px; height: 14px; flex: none; }

  .person {
    position: absolute;
    right: 14px;
    top: 176px;
    text-align: right;
  }
  .person__name {
    font-weight: 700;
    font-size: 16.5px;
    letter-spacing: 1.5px;
    color: var(--accent);
  }
  .person__role {
    font-size: 10px;
    letter-spacing: 1.2px;
    color: var(--text-soft);
  }

  .divider {
    position: absolute;
    left: 12px;
    right: 14px;
    top: 216px;
    height: 1px;
    background: var(--text-soft);
  }
  .address {
    position: absolute;
    left: 12px;
    top: 224px;
    display: flex;
    align-items: center;
    gap: 7px;
    font-size: 10.5px;
    letter-spacing: 1px;
    color: var(--text-soft);
  }
</style>
</head>
<body>
<main class="canvas">

  <section class="card card--front" aria-label="Card front">
    <div class="band band--top band--top-right-cut"></div>
    <h1 class="wordmark">Maple Roster</h1>
    <div class="band band--bottom band--bottom-left-cut"></div>
  </section>

  <section class="card card--back" aria-label="Card back">
    <div class="band band--top band--top-right-cut"></div>
    <h2 class="wordmark">Maple Roster</h2>

    <ul class="contact-list">
      <li>
        <svg class="icon" viewBox="0 0 24 24" aria-hidden="true"><path fill="none" stroke="#38b6de" stroke-width="2" d="M5 3h4l2 5-2.5 1.5a11 11 0 0 0 6 6L16 13l5 2v4a2 2 0 0 1-2 2A16 16 0 0 1 3 5a2 2 0 0 1 2-2z"/></svg>
        041-555-0187
      </li>
      <li>
        <svg class="icon" viewBox="0 0 24 24" aria-hidden="true"><rect x="2" y="5" width="20" height="14" fill="#38b6de"/><path d="M2 5l10 8 10-8" fill="none" stroke="#3f3f40" stroke-width="1.6"/></svg>
        hello@mapleroster.com
      </li>
      <li>
        <svg class="icon" viewBox="0 0 24 24" aria-hidden="true"><g fill="none" stroke="#38b6de" stroke-width="1.6"><circle cx="12" cy="12" r="9"/><ellipse cx="12" cy="12" rx="4" ry="9"/><path d="M3 12h18M5 7h14M5 17h14"/></g></svg>
        www.mapleroster.com
      </li>
    </ul>

    <div class="person">
      <p class="person__name">Daniel Okafor</p>
      <p class="person__role">General Manager</p>
    </div>

    <div class="divider"></div>

    <p class="address">
      <svg class="icon" viewBox="0 0 24 24" aria-hidden="true"><path d="M12 2a6 6 0 0 0-6 6c0 4.5 6 11 6 11s6-6.5 6-11a6 6 0 0 0-6-6z" fill="#38b6de"/><circle cx="12" cy="8" r="2.2" fill="#3f3f40"/><ellipse cx="12" cy="21" rx="6" ry="1.6" fill="none" stroke="#38b6de" stroke-width="1.4"/></svg>
      42 Cedar Grove Road Fairview, VA 20100
    </p>

    <div class="band band--bottom band--top-right-cut"></div>
  </section>

</main>
</body>
</html>
```